Luxury Business Card Design for High-End Window Treatments

Gilded Slatworks
Custom Plantation Shutters & Architectural Shading Systems

⸻

BACK

Daniel Trevick
Owner

Custom Interior & Exterior Window Treatments

919-555-0148
gildedslatworks.com

I have included a picture that I’m hoping we can use on the back, but I’m also wondering if you can get rid of the ladder? Should we get rid of shutters , shades and blinds underneath Gilded Slatworks?

Target Market(s)

High-end residential homeowners, custom home builders, architects, interior designers, and luxury renovation clients seeking premium plantation shutters and motorized architectural shading systems.

Industry/Entity Type

Custom Window treatments

Contact Information for Business Card

Front Gilded Slatworks Custom Plantation Shutters Motorized Architectural Shading Systems BACK Daniel Trevick Owner 919-555-0148 GildedSlatworks.com Custom Interior & Exterior Window Treatments By Appointment

Requirements
Nice to have
• Not 100% sure on nice to halves or the color but you can definitely check out my website to get a better understanding of what I’m trying to do

```html
<!DOCTYPE html>
<html lang="en">
<head>
<meta charset="utf-8">
<title>Gilded Slatworks – Business Card</title>
<link rel="stylesheet" href="https://fonts.googleapis.com/css2?family=Josefin+Sans:wght@300;400&family=Poppins:wght@300;400;600&display=swap">
<style>
  :root {
    --backdrop: #6179b0;
    --card-cream: #e6e1d8;
    --card-dark: #48443d;
    --ink: #2f2c28;
    --ink-soft: #4a463f;
    --rule: #8a847a;
  }
  * { margin: 0; padding: 0; box-sizing: border-box; }
  html, body {
    width: 1200px;
    height: 1200px;
    overflow: hidden;
    background: var(--backdrop);
  }
  .canvas {
    width: 1200px;
    height: 1200px;
    display: flex;
    flex-direction: column;
    align-items: center;
    justify-content: center;
    gap: 60px;
  }
  .card {
    position: relative;
    width: 770px;
    height: 440px;
    background: var(--card-cream);
    overflow: hidden;
    box-shadow: 0 10px 30px rgba(20, 30, 60, 0.25);
  }

  /* Front */
  .front-band {
    position: absolute;
    left: 0; top: 0;
    width: 100%;
    height: 196px;
    background: var(--card-dark);
    display: flex;
    align-items: center;
    justify-content: center;
  }
  .brand-name {
    font-family: "Josefin Sans", sans-serif;
    font-weight: 300;
    font-size: 60px;
    letter-spacing: 4px;
    color: var(--card-cream);
    padding-top: 70px;
  }
  .front-rule {
    position: absolute;
    left: 0; top: 206px;
    width: 100%;
    height: 1px;
    background: var(--rule);
  }
  .tagline {
    position: absolute;
    left: 0; top: 292px;
    width: 100%;
    text-align: center;
    font-family: "Poppins", sans-serif;
    font-weight: 400;
    font-size: 19px;
    line-height: 1.45;
    letter-spacing: 0.6px;
    color: var(--ink-soft);
  }

  /* Back */
  .louver-stripes {
    position: absolute;
    left: 0; top: 0;
    width: 100%;
    height: 220px;
  }
  .louver-stripes rect { fill: var(--card-dark); }
  .contact-block {
    position: absolute;
    left: 0; top: 226px;
    width: 100%;
    text-align: center;
    font-family: "Poppins", sans-serif;
    color: var(--ink);
  }
  .person-name {
    font-weight: 600;
    font-size: 36px;
    line-height: 1.15;
  }
  .person-role {
    font-weight: 400;
    font-size: 15px;
    color: var(--ink-soft);
    margin-top: 2px;
  }
  .contact-rule {
    width: 260px;
    height: 1px;
    background: var(--rule);
    margin: 10px auto 8px;
  }
  .phone {
    font-weight: 400;
    font-size: 30px;
    line-height: 1.2;
  }
  .website {
    font-weight: 400;
    font-size: 32px;
    line-height: 1.25;
  }
</style>
</head>
<body>
  <main class="canvas">
    <section class="card card-front" aria-label="Business card front">
      <div class="front-band">
        <h1 class="brand-name">Gilded Slatworks</h1>
      </div>
      <div class="front-rule"></div>
      <p class="tagline">Custom Plantation Shutters &amp;<br>Motorized Architectural Shading Systems</p>
    </section>

    <section class="card card-back" aria-label="Business card back">
      <svg class="louver-stripes" viewBox="0 0 770 220" preserveAspectRatio="none" aria-hidden="true">
        <rect x="0" y="0" width="770" height="12"/>
        <rect x="0" y="40" width="770" height="24"/>
        <rect x="0" y="92" width="770" height="24"/>
        <rect x="0" y="144" width="770" height="24"/>
        <rect x="0" y="196" width="770" height="24"/>
      </svg>
      <div class="contact-block">
        <h2 class="person-name">Daniel Trevick</h2>
        <p class="person-role">Custom Interior &amp; Exterior Window Treatment</p>
        <div class="contact-rule"></div>
        <p class="phone">919-555-0148</p>
        <p class="website">GildedSlatworks.com</p>
      </div>
    </section>
  </main>
</body>
</html>
```